Automotive component supplier needs a business card design

We need a business card design for our company called Velran Global Components Ltd based in the UK. We are a supplier of interior and exterior components to premium car manufacturers such as Corvel Ashby, Hadley Fenn, Marquist and Tavarelli. We would like to see a modern business card design that uses the colour blue.

Target Market(s)

Premium automotive car manufacturers.

Industry/Entity Type

Automotive

Contact Information for Business Card

Company Name : Velran Global Components Limited
Address: 17 Marlow Yard, Upper Heath, Warwick, CV31 8QL, United Kingdom
Web Address : www.velrancomponents-example.co.uk

Font styles to use
Other font styles liked:
• Helvetica

Colors
3176b5
0255a3
85acd3
cfdeed
cee9f5
85cae6
34a6d7
0692cd
9bcb3c

Requirements
Must have
• Clear company logo and a mixture of blue colours.
Nice to have
• A high quality modern image.
Should not have
• Multiple colours.

```html
<!DOCTYPE html>
<html lang="en">
<head>
<meta charset="utf-8">
<title>Velran Global Components – Business Card</title>
<link rel="stylesheet" href="https://fonts.googleapis.com/css2?family=Arimo:wght@400;700&display=swap">
<style>
  :root {
    --page: #3b3b3b;
    --paper: #f4f4f4;
    --paper-edge: #e6e6e6;
    --blue: #0a86c6;
    --blue-deep: #0476b3;
    --blue-light: #1596d3;
    --green: #8fbf2e;
    --ink: #5b5b5b;
    --white: #ffffff;
  }
  * { box-sizing: border-box; margin: 0; padding: 0; }
  html, body { width: 1200px; height: 965px; overflow: hidden; }
  body { background: var(--page); font-family: "Arimo", Helvetica, Arial, sans-serif; position: relative; }

  .card { position: absolute; left: 246px; width: 710px; height: 404px; overflow: hidden; box-shadow: 0 4px 14px rgba(0,0,0,.45); }
  .card--front { top: 60px; background: radial-gradient(ellipse at 40% 35%, #fbfbfb 0%, var(--paper) 55%, var(--paper-edge) 100%); }
  .card--back { top: 504px; background: radial-gradient(ellipse at 50% 30%, var(--blue-light) 0%, var(--blue) 55%, var(--blue-deep) 100%); }

  .wave { position: absolute; left: 0; bottom: 0; width: 710px; height: 404px; }

  .brand { position: absolute; font-weight: 700; color: var(--blue); line-height: 1; display: flex; flex-direction: column; white-space: nowrap; }
  .brand__name { letter-spacing: 2px; }
  .brand__sub { letter-spacing: 3.2px; }
  .brand__row { display: flex; align-items: center; gap: 10px; }
  .brand__dot { width: 14px; height: 14px; background: currentColor; }

  .card--front .brand { left: 44px; top: 140px; }
  .card--front .brand__name { font-size: 62px; }
  .card--front .brand__sub { font-size: 17.5px; margin-top: 10px; }

  .card--back .brand { left: 0; width: 710px; top: 128px; align-items: center; color: var(--white); }
  .card--back .brand__name { font-size: 96px; }
  .card--back .brand__dot { width: 20px; height: 20px; }
  .card--back .brand__sub { font-size: 27px; margin-top: 14px; letter-spacing: 4.6px; }

  .divider { position: absolute; left: 396px; top: 64px; width: 2px; height: 242px; background: var(--blue); }
  .divider::before { content: ""; position: absolute; left: 0; top: 0; width: 4px; height: 46px; background: var(--green); border-radius: 0 3px 3px 0; }

  .person { position: absolute; left: 420px; top: 66px; white-space: nowrap; }
  .person__name { font-size: 23px; font-weight: 700; color: var(--blue); letter-spacing: .3px; }
  .person__role { font-size: 16px; color: var(--green); margin-top: 3px; }

  .contact { position: absolute; left: 420px; top: 145px; list-style: none; }
  .contact li { display: flex; align-items: center; gap: 9px; font-size: 14px; color: var(--ink); height: 20.5px; white-space: nowrap; }
  .contact svg { width: 15px; height: 15px; flex: none; fill: var(--blue); }

  .address { position: absolute; left: 420px; top: 250px; font-style: normal; font-size: 15.5px; line-height: 20px; color: var(--ink); white-space: nowrap; }

  .site { position: absolute; left: 0; width: 710px; top: 368px; display: flex; align-items: center; justify-content: center; gap: 18px; color: #e8f4fb; font-size: 16px; white-space: nowrap; }
  .site__rule { width: 150px; height: 1px; }
  .site__rule--l { background: linear-gradient(to right, transparent, rgba(255,255,255,.8)); }
  .site__rule--r { background: linear-gradient(to left, transparent, rgba(255,255,255,.8)); }
</style>
</head>
<body>

<section class="card card--front" aria-label="Business card front">
  <svg class="wave" viewBox="0 0 710 404" aria-hidden="true">
    <path d="M0 338 C120 300 300 340 460 378 C580 402 680 385 710 334 L710 404 L0 404 Z" fill="var(--green)"/>
    <path d="M0 357 C140 330 320 358 470 384 C590 400 680 395 710 360 L710 404 L0 404 Z" fill="#ffffff"/>
    <path d="M0 361 C140 335 320 362 470 388 C590 403 680 399 710 366 L710 404 L0 404 Z" fill="var(--blue)"/>
  </svg>

  <div class="brand">
    <div class="brand__row"><span class="brand__dot"></span><span class="brand__name">VELRAN</span></div>
    <span class="brand__sub">GLOBAL COMPONENTS</span>
  </div>

  <div class="divider"></div>

  <div class="person">
    <p class="person__name">DANIEL ROWE</p>
    <p class="person__role">Founder &amp; CEO</p>
  </div>

  <ul class="contact">
    <li><svg viewBox="0 0 16 16"><rect x="1" y="2" width="4" height="12" rx="1"/><rect x="6" y="3" width="9" height="11" rx="1"/><rect x="8" y="5" width="5" height="2" fill="#fff"/></svg>+ 041 730 18 46</li>
    <li><svg viewBox="0 0 16 16"><path d="M4 1h8v14H4z"/><rect x="5.5" y="3" width="5" height="8" fill="#fff"/><circle cx="8" cy="13" r="0.9" fill="#fff"/></svg>+ 0164 552 09 37</li>
    <li><svg viewBox="0 0 16 16"><rect x="1" y="3" width="14" height="10"/><path d="M1.5 3.5 8 9l6.5-5.5" fill="none" stroke="#fff" stroke-width="1.3"/></svg>info@velrancomponents-example.co.uk</li>
    <li><svg viewBox="0 0 16 16"><circle cx="8" cy="8" r="6.6" fill="none" stroke="var(--blue)" stroke-width="1.3"/><ellipse cx="8" cy="8" rx="2.8" ry="6.6" fill="none" stroke="var(--blue)" stroke-width="1.1"/><path d="M1.5 8h13M2.5 4.8h11M2.5 11.2h11" stroke="var(--blue)" stroke-width="1"/></svg>www.velrancomponents-example.co.uk</li>
  </ul>

  <address class="address">17 Marlow Yard, Upper Heath,<br>Warwick, CV31 8QL,<br>United Kingdom</address>
</section>

<section class="card card--back" aria-label="Business card back">
  <div class="brand">
    <div class="brand__row"><span class="brand__dot"></span><span class="brand__name">VELRAN</span></div>
    <span class="brand__sub">GLOBAL COMPONENTS</span>
  </div>
  <div class="site">
    <span class="site__rule site__rule--l"></span>
    <span>www.velrancomponents-example.co.uk</span>
    <span class="site__rule site__rule--r"></span>
  </div>
</section>

</body>
</html>
```